Brell Stone Company Business Cards

Front and Back Business Card - logo and text setup - cool design. I need workable photoshop or illustrator files so I can setup each employee card with design that is created
Updates

Hi everyone, thank you for the great entries. Please no more white and blue cards - there are so many already - black and silver only now please. thanks!

Target Market(s)

Construction Industry - Facility Managers

Industry/Entity Type

Construction

Contact Information for Business Card

I really like contemporary simplistic looks - clean neat....not opposed to seeing some black backrounds

Requirements
Must have
• Logo/website address with design on front only - www.brellstone-example.com (logo attached)
• Back:
• Name/Title/Company Address/Phone/email address
Nice to have
• Cool design
Should not have
• Nothing gimmicky like Fire or Water - since we are a Fire Protection company - it has all been done

```html
<!DOCTYPE html>
<html lang="en">
<head>
<meta charset="utf-8">
<title>Brell Stone Company Business Cards</title>
<link rel="stylesheet" href="https://fonts.googleapis.com/css2?family=Lato:wght@400;700;900&family=Open+Sans:wght@400;600&display=swap">
<style>
  :root {
    --backdrop: #ecebe8;
    --black: #161718;
    --silver: #c8cacd;
    --silver-light: #dfe1e3;
    --silver-dark: #6d7176;
    --white: #ffffff;
    --rule: rgba(200, 202, 205, 0.6);
  }
  * { margin: 0; padding: 0; box-sizing: border-box; }
  html, body {
    width: 1200px;
    height: 900px;
    overflow: hidden;
    background: var(--backdrop);
  }
  .canvas {
    position: relative;
    width: 1200px;
    height: 900px;
  }
  .card {
    position: absolute;
    width: 556px;
    height: 343px;
  }
  .card--contact {
    left: 330px;
    top: 90px;
    background: var(--black);
    color: var(--white);
    text-align: center;
    font-family: "Open Sans", sans-serif;
  }
  .card--brand {
    left: 330px;
    top: 469px;
    background: linear-gradient(135deg, var(--silver-light) 0%, var(--silver) 100%);
  }
  .person-name {
    position: absolute;
    top: 76px;
    left: 0;
    width: 100%;
    font-family: "Lato", sans-serif;
    font-weight: 700;
    font-size: 20px;
    letter-spacing: 0.2px;
    line-height: 24px;
  }
  .person-title {
    position: absolute;
    top: 97px;
    left: 0;
    width: 100%;
    font-size: 16px;
    line-height: 20px;
    color: var(--silver);
  }
  .divider {
    position: absolute;
    left: 180px;
    width: 195px;
    height: 1px;
    background: var(--rule);
  }
  .divider--upper { top: 127px; }
  .divider--lower { top: 210px; }
  .contact-list {
    position: absolute;
    top: 137px;
    left: 0;
    width: 100%;
    list-style: none;
    font-size: 16px;
    line-height: 20px;
  }
  .contact-list b { font-weight: 600; color: var(--silver); }
  .address {
    position: absolute;
    top: 222px;
    left: 0;
    width: 100%;
    font-style: normal;
    font-size: 16px;
    line-height: 20px;
  }
  .brand-mark {
    position: absolute;
    top: 120px;
    left: 0;
    width: 100%;
    display: flex;
    align-items: center;
    justify-content: center;
    gap: 14px;
  }
  .brand-mark__square {
    width: 22px;
    height: 22px;
    background: var(--black);
  }
  .brand-mark__name {
    font-family: "Lato", sans-serif;
    font-weight: 900;
    font-size: 54px;
    line-height: 64px;
    color: var(--black);
    letter-spacing: -0.5px;
  }
  .brand-url {
    position: absolute;
    top: 284px;
    left: 0;
    width: 100%;
    text-align: center;
    font-family: "Open Sans", sans-serif;
    font-weight: 600;
    font-size: 16px;
    color: var(--black);
  }
  .brand-url__accent { color: var(--silver-dark); }
</style>
</head>
<body>
  <main class="canvas">
    <section class="card card--contact" aria-label="Business card, contact side">
      <h1 class="person-name">DANIEL HARTLEY</h1>
      <p class="person-title">Managing Director</p>
      <div class="divider divider--upper"></div>
      <ul class="contact-list">
        <li><b>P:</b> 044-987 654 321</li>
        <li><b>E:</b> info@brellstone-example.com</li>
        <li><b>W:</b> www.brellstone-example.com</li>
      </ul>
      <div class="divider divider--lower"></div>
      <address class="address">12345, Address Goes Here<br>Country Name, 123456.</address>
    </section>

    <section class="card card--brand" aria-label="Business card, brand side">
      <div class="brand-mark">
        <span class="brand-mark__square"></span>
        <span class="brand-mark__name">Brell Stone</span>
      </div>
      <p class="brand-url">www.<span class="brand-url__accent">brellstone-example</span>.com</p>
    </section>
  </main>
</body>
</html>
```